Business Card Design Project

Require a business card for a swing band called "Brass and Velvet". We are a 6 piece band that performs at events and corporate functions. Our music is great for dancing to or just providing a classy background atmosphere for people to enjoy. Final design should communicate professionalism and style with a hint of fun.

Sorry, just realised that it needs to be single sided only. Also, no rounded edges.

Industry/Entity Type

Events

Requirements
Must have
• Contact number: 0438 216 903
email address: brassandvelvet@mailbox-example.net
Website details: www.brassandvelvet-example.com

```html
<!DOCTYPE html>
<html lang="en">
<head>
<meta charset="utf-8">
<title>Brass and Velvet — Business Card</title>
<link rel="stylesheet" href="https://fonts.googleapis.com/css2?family=Merriweather:wght@300&display=swap">
<style>
  :root {
    --page: #ffffff;
    --card: #000000;
    --ink: #ffffff;
    --art-light: #d9d9d9;
    --art-dark: #1a1a1a;
  }
  * { margin: 0; padding: 0; box-sizing: border-box; }
  html, body {
    width: 1200px;
    height: 644px;
    overflow: hidden;
    background: var(--page);
  }
  .canvas {
    position: relative;
    width: 1200px;
    height: 644px;
    background: var(--page);
  }
  .business-card {
    position: absolute;
    left: 0;
    top: 26px;
    width: 943px;
    height: 550px;
    background: var(--card);
    overflow: hidden;
    color: var(--ink);
    font-family: "Merriweather", Georgia, serif;
    font-weight: 300;
  }
  .band-name {
    position: absolute;
    left: 48px;
    top: 48px;
    font-size: 60px;
    line-height: 1.05;
    color: var(--ink);
    font-weight: 300;
  }
  .band-name span { display: block; }
  .band-name .line-2 { padding-left: 230px; }
  .band-name .line-3 { padding-left: 310px; }
  .contact-details {
    position: absolute;
    left: 47px;
    top: 397px;
    list-style: none;
    font-size: 27px;
    line-height: 36px;
    letter-spacing: 0.2px;
  }
  .cocktail-sax-art {
    position: absolute;
    left: 590px;
    top: 0;
    width: 353px;
    height: 550px;
  }
</style>
</head>
<body>
  <main class="canvas">
    <section class="business-card">
      <h1 class="band-name">
        <span class="line-1">Brass</span>
        <span class="line-2">and</span>
        <span class="line-3">Velvet</span>
      </h1>

      <ul class="contact-details">
        <li class="contact-phone">0438 216 903</li>
        <li class="contact-web">www.brassandvelvet-example.com</li>
        <li class="contact-email">brassandvelvet@mailbox-example.net</li>
      </ul>

      <svg class="cocktail-sax-art" viewBox="0 0 353 550" role="img"
           aria-label="White line illustration of a cocktail glass with a straw and lemon slice in front of a saxophone">
        <defs>
          <radialGradient id="art-glow" cx="45%" cy="55%" r="60%">
            <stop offset="0%" stop-color="var(--art-light)" stop-opacity="0.55"/>
            <stop offset="100%" stop-color="var(--art-dark)" stop-opacity="0"/>
          </radialGradient>
        </defs>
        <rect width="353" height="550" fill="url(#art-glow)"/>
      </svg>
    </section>
  </main>
</body>
</html>
```